Quillmarsh Property Solutions need a business card design

Hello guys. We would need a business card design asap please.
We are a start up property investment business based in London UK specialised in buying, selling, managing and letting properties and helping distressed property owners.
The name of our Business is Quillmarsh, the logo symbolises the four fundamental elements of the world (earth, air, fire and water) and so it stands for strength, stability, longevity.
We would like the business card to communicate professionalism and reliability. Many many thanks indeed for your work.

Details:

1.) Rosalind Updike
Property Investor
Mobile: +44(0)7700123456
Email: rosalind.quillmarsh@mailbox-example.com

2.) Dominic Updike
Property Investor
Mobile: +44(0)7700987654
Email: dominic.quillmarsh@mailbox-example.com

```html
<!DOCTYPE html>
<html lang="en">
<head>
<meta charset="utf-8">
<title>Quillmarsh Property Solutions – Business Card</title>
<link rel="stylesheet" href="https://fonts.googleapis.com/css2?family=Open+Sans:wght@400;600&family=Montserrat:wght@700;800&display=swap">
<style>
  :root {
    --backdrop: #e9e6e1;
    --card: #ffffff;
    --ink: #1c1c1c;
    --muted: #4a4a4a;
    --name-blue: #2f6fd0;
    --band-blue: #3a78d8;
    --band-green: #1f9a49;
    --divider: #c9c9c9;
    --ghost: #9a9a9a;
    --shadow: rgba(0, 0, 0, 0.18);
  }
  * { box-sizing: border-box; margin: 0; padding: 0; }
  html, body { width: 1200px; height: 720px; overflow: hidden; }
  body {
    background: var(--backdrop);
    font-family: "Open Sans", Arial, sans-serif;
    display: flex;
    align-items: center;
    justify-content: center;
    gap: 40px;
  }
  .card {
    position: relative;
    width: 540px;
    height: 309px;
    background: var(--card);
    box-shadow: 0 6px 18px var(--shadow);
    overflow: hidden;
  }

  /* Front */
  .card-front__wave { position: absolute; inset: 0; width: 100%; height: 100%; }
  .brand {
    position: absolute;
    left: 34px;
    top: 96px;
    width: 200px;
    display: flex;
    align-items: center;
    gap: 10px;
  }
  .brand__mark { width: 14px; height: 14px; background: var(--ink); flex: none; }
  .brand__name {
    font-family: "Montserrat", Arial, sans-serif;
    font-weight: 800;
    color: var(--ink);
    font-size: 21px;
    line-height: 1.1;
    letter-spacing: 0.5px;
    text-transform: uppercase;
  }
  .brand__name small { display: block; font-size: 10.5px; letter-spacing: 1px; }
  .divider {
    position: absolute;
    left: 262px;
    top: 34px;
    width: 1px;
    height: 80px;
    background: var(--divider);
  }
  .contact { position: absolute; left: 276px; top: 34px; }
  .contact__name { color: var(--name-blue); font-weight: 600; font-size: 15px; }
  .contact__role { color: var(--muted); font-size: 11px; margin-bottom: 8px; }
  .contact__line {
    display: flex;
    align-items: center;
    gap: 6px;
    color: var(--muted);
    font-size: 11px;
    margin-top: 4px;
  }
  .contact__icon { width: 11px; height: 11px; flex: none; }

  /* Back */
  .card-back { display: flex; flex-direction: column; align-items: center; justify-content: center; }
  .ghost-name {
    font-family: "Montserrat", Arial, sans-serif;
    font-weight: 700;
    color: var(--ghost);
    text-transform: uppercase;
    text-align: center;
    line-height: 1.05;
    margin-top: -20px;
  }
  .ghost-name__main { display: block; font-size: 46px; letter-spacing: 2px; }
  .ghost-name__sub { display: block; font-size: 22px; letter-spacing: 1.5px; }
  .website {
    position: absolute;
    bottom: 30px;
    width: 100%;
    text-align: center;
    color: var(--muted);
    font-size: 15px;
    letter-spacing: 0.5px;
  }
</style>
</head>
<body>
  <section class="card card-front" aria-label="Business card front">
    <svg class="card-front__wave" viewBox="0 0 540 309" preserveAspectRatio="none" aria-hidden="true">
      <path d="M0 309 L0 262 C120 262 210 250 290 215 C370 180 450 168 540 160 L540 182 C450 190 380 206 300 240 C220 274 120 292 0 296 Z" fill="var(--band-blue)"/>
      <path d="M0 258 C120 258 205 244 285 208 C365 172 450 158 540 152 L540 158 C450 165 368 178 290 213 C210 248 120 262 0 264 Z" fill="var(--band-green)"/>
    </svg>

    <div class="brand">
      <span class="brand__mark"></span>
      <span class="brand__name">Quillmarsh<small>Property Solutions</small></span>
    </div>

    <div class="divider"></div>

    <div class="contact">
      <p class="contact__name">Rosalind Updike</p>
      <p class="contact__role">Property Investor</p>
      <p class="contact__line">
        <svg class="contact__icon" viewBox="0 0 12 12" aria-hidden="true"><rect x="3" y="0.5" width="6" height="11" rx="1.2" fill="var(--name-blue)"/><rect x="4" y="2" width="4" height="6" fill="#fff"/></svg>
        +44(0)7700123456
      </p>
      <p class="contact__line">
        <svg class="contact__icon" viewBox="0 0 12 12" aria-hidden="true"><circle cx="6" cy="6" r="6" fill="var(--name-blue)"/><rect x="2.8" y="4" width="6.4" height="4.4" fill="#fff"/><path d="M2.8 4 L6 6.6 L9.2 4" stroke="var(--name-blue)" stroke-width="0.8" fill="none"/></svg>
        rosalind.quillmarsh@mailbox-example.com
      </p>
    </div>
  </section>

  <section class="card card-back" aria-label="Business card back">
    <p class="ghost-name">
      <span class="ghost-name__main">Quillmarsh</span>
      <span class="ghost-name__sub">Property Solutions</span>
    </p>
    <p class="website">www.quillmarsh-example.com</p>
  </section>
</body>
</html>
```